The design should look similar to the uploaded example to accommodate the information needed for a business card template. I would like to see the colors orange and charcoal grey incorporated along with the logo.The following should be on the back of the card SPECIALIZING IN NEW AND USED TIRES & WHEELS FOR:- Loaders- Skid Steers- Telehandlers- Boom Lifts- Forklifs and moreELIMINATING DOWNTIMEWheel Exchange Program for New & Used Foam Filled and Solid Rubber TiresSPECIALTY SERVICES- Foam Filling Tires- Largest Tire Press in SE- ONSITE Forklift Tire Press- Boom Truck Services - Rubber Tracks

Target Market(s)

New and Existing Customers

Industry/Entity Type

Business

Contact Information for Business Card

NAMEHEAVY DUTY TIRE, LLC8470 Belvedere RoadWest Palm Beach, FL 33411P: 844-HD-TIRESF: 561-431-6469C:E: W: WWW.GRANITERIMSUPPLY-EXAMPLE.COM

Font styles to use
Sans Serif

Colors
f37122
333333

Requirements
Must have
• The logo and the information indicated for the backside of the card
Nice to have
• Keep the orange and charcoal grey colors

```html
<!DOCTYPE html>
<html lang="en">
<head>
<meta charset="utf-8">
<title>Granite Rim Supply — Business Card</title>
<link rel="stylesheet" href="https://fonts.googleapis.com/css2?family=Open+Sans:wght@400;600;700&display=swap">
<style>
  :root {
    --orange: #f37122;
    --charcoal: #313b38;
    --ink: #1f1f1f;
    --paper: #ffffff;
    --backdrop: #2a2b2e;
    --light-text: #f2f2f2;
  }
  * { box-sizing: border-box; margin: 0; padding: 0; }
  html, body { width: 1200px; height: 864px; overflow: hidden; }
  body {
    background: var(--backdrop);
    font-family: "Open Sans", Arial, sans-serif;
    display: flex; flex-direction: column; align-items: center; justify-content: center;
    gap: 44px;
  }
  .card {
    width: 580px; height: 330px; position: relative; overflow: hidden;
    box-shadow: 0 10px 24px rgba(0,0,0,.45);
  }
  /* Back side */
  .card--back { background: var(--charcoal); color: var(--light-text); }
  .services {
    position: absolute; top: 40px; left: 40px; width: 230px; text-align: right;
  }
  .specialties {
    position: absolute; top: 64px; left: 318px; width: 240px;
  }
  .heading {
    color: var(--orange); font-weight: 700; font-size: 15px; letter-spacing: .02em;
    line-height: 1.2; text-transform: uppercase; margin-bottom: 8px;
  }
  .list { list-style: none; font-size: 13px; line-height: 19px; font-weight: 600; }
  .list li::after, .list--left li::before {
    content: ""; display: inline-block; width: 6px; height: 6px; border-radius: 50%;
    background: var(--orange); vertical-align: middle;
  }
  .list li::after { margin-left: 8px; }
  .list--left li::after { content: none; }
  .list--left li::before { margin-right: 6px; }
  .downtime {
    position: absolute; left: 0; right: 0; top: 222px; text-align: center;
  }
  .downtime .heading { margin-bottom: 2px; }
  .downtime p { font-size: 13px; font-weight: 600; line-height: 17px; }

  /* Front side */
  .card--front { background: var(--paper); color: var(--ink); }
  .brand {
    position: absolute; top: 50px; left: 0; right: 0;
    display: flex; align-items: center; justify-content: center; gap: 10px;
  }
  .brand__dot { width: 22px; height: 22px; border-radius: 50%; background: var(--orange); }
  .brand__name {
    font-size: 30px; font-weight: 700; color: var(--charcoal); letter-spacing: .02em;
  }
  .contact {
    position: absolute; top: 178px; left: 10px; width: 262px; list-style: none;
    text-align: right; font-size: 13px; line-height: 21px;
  }
  .contact li {
    display: flex; justify-content: flex-end; align-items: center; gap: 9px;
    white-space: nowrap;
  }
  .contact svg { width: 12px; height: 12px; fill: var(--orange); flex: none; }
  .identity { position: absolute; top: 196px; left: 312px; }
  .identity__name { color: var(--orange); font-size: 19px; font-weight: 600; margin-left: 10px; margin-bottom: 12px; }
  .identity__company { color: var(--orange); font-size: 15px; font-weight: 700; margin-bottom: 4px; }
  .identity__address { font-size: 14px; line-height: 20px; font-style: normal; }
</style>
</head>
<body>
  <section class="card card--back" aria-label="Card back">
    <div class="services">
      <h2 class="heading">Specialty Services</h2>
      <ul class="list">
        <li>Foam Filling Tires</li>
        <li>Largest Tire Press in SE</li>
        <li>ONSITE Forklift Tire Press</li>
        <li>Boom Truck Services</li>
        <li>Rubber Tracks</li>
      </ul>
    </div>
    <div class="specialties">
      <h2 class="heading">Specializing in new and<br>used tires &amp; wheels for:</h2>
      <ul class="list list--left">
        <li>Loaders</li>
        <li>Skid Steers</li>
        <li>TelehandlersBoom Lifts</li>
        <li>Forklifs and more</li>
      </ul>
    </div>
    <div class="downtime">
      <h2 class="heading">Eliminating Downtime</h2>
      <p>Wheel Exchange Program for New &amp; Used Foam<br>Filled and Solid Rubber Tires</p>
    </div>
  </section>

  <section class="card card--front" aria-label="Card front">
    <div class="brand">
      <span class="brand__dot"></span>
      <span class="brand__name">GRANITE RIM</span>
    </div>
    <ul class="contact">
      <li>844-GR-WHEEL
        <svg viewBox="0 0 12 12"><path d="M2.5 1l2 2.2-1 1.3c.7 1.5 1.6 2.4 3 3l1.3-1 2.2 2-1 1.5C5.5 10 2 6.5 1 3.5z"/></svg></li>
      <li>561-278-9053
        <svg viewBox="0 0 12 12"><path d="M3 1h5v3H3zM1 5h10v6H1zm2 2v1h2V7zm4 0v1h2V7z"/></svg></li>
      <li>123-456-7890
        <svg viewBox="0 0 12 12"><path d="M1.5 2h9v8h-9zm1.5 1.5v5h6v-5z"/></svg></li>
      <li>info@graniterim-example.com
        <svg viewBox="0 0 12 12"><path d="M1 2.5h10v7H1zm1 1 4 3 4-3z"/></svg></li>
      <li>www.graniterimsupply-example.com
        <svg viewBox="0 0 12 12"><circle cx="6" cy="6" r="5"/></svg></li>
    </ul>
    <div class="identity">
      <p class="identity__name">Marcus Delaney</p>
      <p class="identity__company">GRANITE RIM SUPPLY, LLC</p>
      <address class="identity__address">5126 Marston Lane<br>Coral Vista, FL 33482</address>
    </div>
  </section>
</body>
</html>
```